Diverse, up-scale salon needs eye-catching, unique business cards.

We are looking for a unique business card design for our stylist but that can also be multi functional and used for appointment reminder and referrals. I will need a design in a format that I can modify names and titles going forward. In the past we have had a dark background with the logo on one side, and stylist and contact information on the other but we are open to all ideas. I have included our mission statement as well as branded colors below. The statement doesn't need to go on the card, it's just a reference for target market. We need space for the stylists name, title, instagram handle and then the salons phone number, website and address. I am also open to adding a spot for a qr code linked to the stylist instagram or the salon booking link.

primary brand colors:
#333333 #233415 #36502a #93874a #000000
Mission statement:
Vessolin Hair Studio, a high-end salon located in the lively Downtown Farmington, Michigan, is committed to providing exceptional services in a welcoming and relaxed environment to meet the needs of our diverse clientele.
Our salon specializes in contemporary custom haircuts, coloring, extensions, and barbering and beard grooming services. Our team of skilled stylists is passionate and inventive in their hair styling techniques. At the heart of our salon are values centered on quality, innovation, creativity, and above all, comfort. These core values are evident in every appointment across our customizable array of services.
Our goal is to establish a benchmark for exceptional hair care for every human.
Website: www.vessolinhairstudio.example
instagram: @vessolinhairstudio
address: 41782 Pelham Crest Rd, Farmington MI
phone: 248-613-4087

Industry/Entity Type

Hair Salon

Contact Information for Business Card

Stylist name, title, phone, instagram, website, address, (optional qr code)

Requirements
Should not have
• Does not need mission statement on the card.

```html
<!DOCTYPE html>
<html lang="en">
<head>
<meta charset="utf-8">
<title>Vessolin Hair Studio — Business Cards</title>
<link href="https://fonts.googleapis.com/css2?family=Cinzel:wght@500&family=Montserrat:wght@400;500&display=swap" rel="stylesheet">
<style>
  :root {
    --backdrop: #3a3a3a;
    --card: #161616;
    --gold: #93874a;
    --ink: #f2f2f2;
    --shadow: rgba(0,0,0,0.45);
  }
  * { box-sizing: border-box; margin: 0; padding: 0; }
  html, body { width: 1200px; height: 801px; overflow: hidden; }
  body {
    background: var(--backdrop);
    font-family: "Montserrat", sans-serif;
    position: relative;
  }
  .card {
    position: absolute;
    top: 246px;
    width: 540px;
    height: 309px;
    background: var(--card);
    border: 2px solid var(--gold);
    box-shadow: 0 14px 30px var(--shadow);
    overflow: hidden;
  }
  .card--back { left: 40px; }
  .card--front { left: 620px; }

  .brand {
    position: absolute;
    display: flex;
    align-items: center;
    gap: 14px;
  }
  .brand__circle {
    width: 58px; height: 58px;
    border: 3px solid var(--gold);
    border-radius: 50%;
    flex: none;
  }
  .brand__name {
    font-family: "Montserrat", sans-serif;
    font-weight: 500;
    color: var(--gold);
    font-size: 15px;
    letter-spacing: 3px;
    text-transform: uppercase;
    line-height: 1.5;
  }
  .card--back .brand { left: 26px; top: 118px; }
  .card--front .brand { right: 34px; top: 118px; }

  .divider {
    position: absolute;
    left: 262px; top: 34px; bottom: 34px;
    width: 1px;
    background: var(--gold);
  }
  .details {
    position: absolute;
    left: 292px; top: 40px;
    color: var(--ink);
  }
  .details__name {
    font-family: "Cinzel", serif;
    font-weight: 500;
    color: var(--gold);
    font-size: 24px;
    letter-spacing: 1px;
    line-height: 1;
  }
  .details__title { font-size: 14px; margin-top: 6px; }
  .details__address { font-size: 13px; line-height: 1.45; margin-top: 22px; }
  .contact { list-style: none; margin-top: 22px; font-size: 13px; }
  .contact li { display: flex; align-items: center; gap: 8px; line-height: 1.65; }
  .contact svg { width: 11px; height: 11px; flex: none; }
</style>
</head>
<body>
  <section class="card card--back" aria-label="Business card, contact side">
    <div class="brand">
      <span class="brand__circle"></span>
      <span class="brand__name">Vessolin<br>Hair Studio</span>
    </div>
    <span class="divider"></span>
    <div class="details">
      <p class="details__name">Marisol</p>
      <p class="details__title">President</p>
      <p class="details__address">41782 Pelham Crest Rd<br>Farmington MI</p>
      <ul class="contact">
        <li>
          <svg viewBox="0 0 12 12" aria-hidden="true"><path fill="#93874a" d="M2.4 1h2l1 2.6-1.3.9a6.5 6.5 0 0 0 3.4 3.4l.9-1.3 2.6 1v2c0 .8-.6 1.4-1.4 1.4A9.6 9.6 0 0 1 1 2.4C1 1.6 1.6 1 2.4 1z"/></svg>
          248-613-4087
        </li>
        <li>
          <svg viewBox="0 0 12 12" aria-hidden="true"><circle cx="6" cy="6" r="5" fill="#93874a"/></svg>
          @vessolinhairstudio
        </li>
        <li>
          <svg viewBox="0 0 12 12" aria-hidden="true"><circle cx="6" cy="6" r="5" fill="#93874a"/></svg>
          www.vessolinhairstudio.example
        </li>
      </ul>
    </div>
  </section>

  <section class="card card--front" aria-label="Business card, brand side">
    <div class="brand">
      <span class="brand__circle"></span>
      <span class="brand__name">Vessolin<br>Hair Studio</span>
    </div>
  </section>
</body>
</html>
```